Home page design for Drone video business (the Business focusses on home videos for realtors)

Dear reader,

*I NEED DESIGNS OF ALL THE PAGES*
We need a first design of a homepage and of 4 other pages of the website of a business that sells drone video services. All the pages will need to be in the similar design style.
The video's are targeted at consumers that want to sell there home and would like to have a cool drone video of photos of their home.

How does the website look:
- has a navbar on top
- A cool looking banner of an areal drone.
- A Big header: with company name: SkyLoftReels
- A smaller subheader: We film your home to increase your chances of sale
- Then a section with a Big header: How does it work
- In this section a place for a vimeo explainitory video
- Then a similar navbar styled bar with a phone number and a email address
- Then a section where the videos porfolio is displayed in a cool way
- Inside this sectiona header: Our work

- A section with header: Why us?
- 4 symbols here with a subheader and some lorum ipsum text underneath (see wireframe images)

- Under that a: Contact us
- where you can put in name, email, phone, message box and a send button

- At the bottom a footer with phone number and a fake address for now.

Be creative. Use creative but serious color.
Use a serious font. Make it a sharp design. Sharp lines. Not to dark design and not to light design.

The wireframes are the same kind of images.
PLEASE PUT IN DESIGNS OF ALL THE PAGES

Good luck

Target Market(s)

People that want to sell home and want to make a cool drone video or photos of their home.

Industry/Entity Type

Business

Contact Information for Business Card

Lucas Wenning
lucas@skyloftreels.example
+31647208351

Logo Text

SkyLoftReels

Number of Pages Required

1 page

Font styles to use
Sans Serif

Requirements
Must have
• All the sections as explained in the instructions.
• The nav bar should have an about us, services, portfolio and a contact us buttons.
• See instruction for details.
• Must include designs of the front page, contact us, our services, portfolio and contact us.
• If you do add some designs for the "about us", "services", "prices", "portfolio" and "contact us" pages, you make a way better chance of winning the competition.
Nice to have
• designs for the other pages as described at the Must haves. You make a better chance of winning if you include them. Look at the wireframes to see the mockups for those pages. think creative about what kind of sections and design should be included in those pages.
Should not have
• bad designs.

```html
<!DOCTYPE html>
<html lang="en">
<head>
<meta charset="utf-8">
<title>SkyLoftReels – Home</title>
<link href="https://fonts.googleapis.com/css2?family=Exo+2:wght@500;600;700&family=Lato:wght@400;700&display=swap" rel="stylesheet">
<style>
:root{
  --red:#a51c24;
  --red-dark:#7d1218;
  --ink:#2a2a2a;
  --muted:#5a5a5a;
  --band:#ededed;
  --panel:#e6e5e3;
  --line:#d6d6d6;
  --white:#ffffff;
  --black:#0c0c0c;
}
*{box-sizing:border-box;margin:0;padding:0}
html,body{width:1200px;height:2539px;overflow:hidden;background:var(--white)}
body{position:relative;font-family:"Lato",sans-serif;color:var(--ink)}
.abs{position:absolute}
.head-font{font-family:"Exo 2",sans-serif}

/* nav */
.nav{left:0;top:0;width:1200px;height:64px;background:var(--white);border-bottom:1px solid var(--line)}
.brand{left:100px;top:16px;font-family:"Exo 2",sans-serif;font-weight:700;font-size:26px;color:var(--ink);letter-spacing:.5px}
.nav-item{top:0;height:64px;line-height:70px;font-family:"Exo 2",sans-serif;font-weight:600;font-size:16px;color:var(--ink);text-align:center}
.nav-item.active{background:var(--red);color:var(--white);border-bottom:4px solid #2a2a2a}

/* hero */
.hero{left:0;top:64px;width:1200px;height:496px;background:linear-gradient(180deg,#7f93a8 0%,#a9b7c3 45%,#8a8f94 75%,#4e545a 100%)}
.hero-title{left:0;width:1200px;top:270px;text-align:center;font-family:"Exo 2",sans-serif;font-weight:600;color:var(--white);text-shadow:0 2px 4px rgba(0,0,0,.35)}
.hero-title h1{font-size:42px;font-weight:600;letter-spacing:.5px}
.hero-title p{font-size:29px;line-height:39px;margin-top:8px}
.dots{left:0;width:1200px;top:533px;text-align:center}
.dots span{display:inline-block;width:9px;height:9px;border-radius:50%;background:rgba(255,255,255,.75);margin:0 3px}
.dots span.on{background:var(--white)}

.section-title{left:0;width:1200px;text-align:center;font-family:"Exo 2",sans-serif;font-weight:600;font-size:34px;color:var(--ink)}
.section-title em{font-style:normal;color:var(--red)}

/* video */
.video{left:271px;top:696px;width:660px;height:377px;background:linear-gradient(180deg,#2c2c2c 0%,#3f6f95 40%,#4aa0cf 100%)}

/* contact band */
.band{left:0;top:1073px;width:1200px;height:114px;background:var(--band)}
.band-text{font-family:"Exo 2",sans-serif;font-weight:600;font-size:24px;color:var(--ink);top:1115px}
.band-divider{left:558px;top:1090px;width:1px;height:80px;background:#cfcfcf}

/* work */
.card{top:1303px;width:293px;height:251px;border:1px solid var(--line);background:var(--white);padding:8px}
.card-img{width:100%;height:100%;position:relative}
.play{position:absolute;left:50%;top:50%;width:52px;height:34px;margin:-17px 0 0 -26px;background:#d51e1e;border-radius:7px}
.play:after{content:"";position:absolute;left:21px;top:10px;border-left:13px solid #fff;border-top:7px solid transparent;border-bottom:7px solid transparent}

/* why us */
.why{left:0;top:1598px;width:1200px;height:491px;background:var(--panel)}
.why-icon{width:110px;height:110px;border-radius:50%;background:var(--red);border:3px solid var(--white);box-shadow:0 0 0 1px #d2d0cd}
.why-icon svg{display:block;margin:25px auto 0}
.why-title{font-family:"Exo 2",sans-serif;font-weight:600;font-size:22px;color:var(--ink)}
.why-text{width:290px;font-size:13.5px;line-height:20px;color:var(--muted)}

/* form */
.field{height:43px;border:1px solid var(--line);background:var(--white);font-size:13.5px;color:var(--muted);padding:12px 11px}
.message{left:124px;top:2275px;width:951px;height:93px;border:1px solid var(--line);font-size:13.5px;color:var(--muted);padding:11px}
.submit{left:535px;top:2395px;width:128px;height:42px;background:var(--red);color:var(--white);font-family:"Exo 2",sans-serif;font-weight:600;font-size:16px;text-align:center;line-height:42px}

/* footer */
.footer{left:0;top:2483px;width:1200px;height:56px;background:var(--black);border-bottom:4px solid var(--red)}
.footer-text{top:2500px;color:var(--white);font-size:16px}
.copyright{right:100px;top:2503px;color:var(--white);font-family:"Exo 2",sans-serif;font-weight:600;font-size:12px}
</style>
</head>
<body>

<header class="abs nav">
  <div class="abs brand">SkyLoftReels</div>
  <div class="abs nav-item active" style="left:496px;width:98px">HOME</div>
  <div class="abs nav-item" style="left:618px;width:90px">SERVICES</div>
  <div class="abs nav-item" style="left:736px;width:110px">ABOUT US</div>
  <div class="abs nav-item" style="left:862px;width:100px">PORTFOLIO</div>
  <div class="abs nav-item" style="left:996px;width:120px">CONTACT US</div>
</header>

<section class="abs hero" role="img" aria-label="City skyline with a red and grey camera drone flying over high-rise towers"></section>
<div class="abs hero-title">
  <h1>SKYLOFTREELS</h1>
  <p>WE FILM YOUR HOME TO<br>INCREASE YOUR CHANCES OF SALE</p>
</div>
<div class="abs dots"><span class="on"></span><span></span><span></span><span></span></div>

<h2 class="abs section-title" style="top:610px">HOW DOES IT <em>WORK?</em></h2>
<div class="abs video" role="img" aria-label="Hands holding a tablet playing an explainer video of a drone over a coastal city"></div>
<svg class="abs" style="left:551px;top:820px" width="100" height="100" viewBox="0 0 100 100" aria-hidden="true">
  <circle cx="50" cy="50" r="50" fill="rgba(255,255,255,.85)"/>
  <path d="M40 30 L72 50 L40 70 Z" fill="#c21d24"/>
</svg>

<div class="abs band"></div>
<svg class="abs" style="left:310px;top:1108px" width="34" height="44" viewBox="0 0 24 30" aria-hidden="true">
  <path d="M5 2 L9 2 L11 9 L8 11 C9 16 12 20 15 22 L18 19 L23 22 L22 27 C20 29 16 29 12 26 C6 21 2 14 2 7 C2 4 3 2 5 2Z" fill="var(--red)"/>
</svg>
<div class="abs band-text" style="left:356px">+31647208351</div>
<div class="abs band-divider"></div>
<svg class="abs" style="left:594px;top:1112px" width="48" height="32" viewBox="0 0 48 32" aria-hidden="true">
  <rect x="1" y="1" width="46" height="30" fill="none" stroke="var(--red)" stroke-width="3"/>
  <path d="M2 2 L24 19 L46 2 M2 30 L18 15 M46 30 L30 15" fill="none" stroke="var(--red)" stroke-width="3"/>
</svg>
<div class="abs band-text" style="left:660px">contact@skyloftreels.example</div>

<h2 class="abs section-title" style="top:1238px">OUR <em>WORK?</em></h2>
<svg class="abs" style="left:42px;top:1400px" width="34" height="60" viewBox="0 0 34 60" aria-hidden="true"><path d="M32 2 L3 30 L32 58" fill="none" stroke="#bdbdbd" stroke-width="2"/></svg>
<svg class="abs" style="left:1125px;top:1400px" width="34" height="60" viewBox="0 0 34 60" aria-hidden="true"><path d="M2 2 L31 30 L2 58" fill="none" stroke="#bdbdbd" stroke-width="2"/></svg>
<div class="abs card" style="left:98px"><div class="card-img" role="img" aria-label="Pilot flying a drone in front of a suburban house" style="background:linear-gradient(180deg,#4f86c6 0%,#8fb4d9 55%,#c9b98e 100%)"><span class="play"></span></div></div>
<div class="abs card" style="left:454px"><div class="card-img" role="img" aria-label="Drone hovering above a two-storey home" style="background:linear-gradient(180deg,#c8d3dc 0%,#d9d3c5 55%,#8c7b66 100%)"><span class="play"></span></div></div>
<div class="abs card" style="left:807px"><div class="card-img" role="img" aria-label="Drone filming a stone house in winter" style="background:linear-gradient(180deg,#9fb3c6 0%,#7b7268 55%,#e6e8ea 100%)"><span class="play"></span></div></div>

<section class="abs why"></section>
<h2 class="abs section-title" style="top:1639px">WHY <em>US?</em></h2>

<div class="abs why-icon" style="left:160px;top:1722px">
  <svg width="56" height="56" viewBox="0 0 56 56" aria-hidden="true" fill="none" stroke="#fff" stroke-width="3"><path d="M14 14 L42 42 M42 14 L14 42"/><circle cx="12" cy="12" r="7"/><circle cx="44" cy="12" r="7"/><circle cx="12" cy="44" r="7"/><circle cx="44" cy="44" r="7"/><rect x="22" y="22" width="12" height="12" fill="#a51c24"/></svg>
</div>
<div class="abs why-title" style="left:293px;top:1718px">CHEAP</div>
<p class="abs why-text" style="left:293px;top:1752px">Lorem ipsum dolor sit amet, consectetuer sit al adipiscing elit, sed diam nonummy nibh dolor euismod tincidunt ut laoreet dolore magna sit aliquam erat volutpat.</p>

<div class="abs why-icon" style="left:625px;top:1722px">
  <svg width="56" height="56" viewBox="0 0 56 56" aria-hidden="true" fill="none" stroke="#fff" stroke-width="3"><circle cx="15" cy="15" r="9"/><circle cx="41" cy="15" r="9"/><circle cx="15" cy="41" r="9"/><circle cx="41" cy="41" r="9"/><circle cx="28" cy="28" r="7" fill="#fff"/></svg>
</div>
<div class="abs why-title" style="left:760px;top:1718px">FLEXIBLE</div>
<p class="abs why-text" style="left:760px;top:1752px">Lorem ipsum dolor sit amet, consectetuer sit al adipiscing elit, sed diam nonummy nibh dolor euismod tincidunt ut laoreet dolore magna sit aliquam erat volutpat.</p>

<div class="abs why-icon" style="left:160px;top:1891px">
  <svg width="60" height="56" viewBox="0 0 60 56" aria-hidden="true"><rect x="6" y="8" width="48" height="32" fill="none" stroke="#fff" stroke-width="3"/><text x="30" y="31" text-anchor="middle" font-family="Exo 2, sans-serif" font-weight="700" font-size="17" fill="#fff">4K</text><path d="M24 40 L22 48 M36 40 L38 48 M18 48 L42 48" stroke="#fff" stroke-width="3"/></svg>
</div>
<div class="abs why-title" style="left:293px;top:1888px">4K QUALITY</div>
<p class="abs why-text" style="left:293px;top:1928px">Lorem ipsum dolor sit amet, consectetuer sit al adipiscing elit, sed diam nonummy nibh dolor euismod tincidunt ut laoreet dolore magna sit aliquam erat volutpat.</p>

<div class="abs why-icon" style="left:625px;top:1891px">
  <svg width="60" height="56" viewBox="0 0 60 56" aria-hidden="true" fill="none" stroke="#fff" stroke-width="3"><path d="M4 14 L22 14 M38 14 L56 14 M13 14 L13 22 M47 14 L47 22"/><rect x="18" y="20" width="24" height="12" fill="#fff"/><path d="M20 32 L14 46 M40 32 L46 46 M10 46 L18 46 M42 46 L50 46"/></svg>
</div>
<div class="abs why-title" style="left:760px;top:1893px">INCREASE SALE CHANCE</div>
<p class="abs why-text" style="left:760px;top:1928px">Lorem ipsum dolor sit amet, consectetuer sit al adipiscing elit, sed diam nonummy nibh dolor euismod tincidunt ut laoreet dolore magna sit aliquam erat volutpat.</p>

<h2 class="abs section-title" style="top:2138px">CONTACT <em>US</em></h2>
<div class="abs field" style="left:124px;top:2209px;width:299px">Name</div>
<div class="abs field" style="left:449px;top:2209px;width:299px">Name</div>
<div class="abs field" style="left:775px;top:2209px;width:300px">Name</div>
<div class="abs message">Message</div>
<div class="abs submit">SUBMIT</div>

<footer class="abs footer"></footer>
<svg class="abs" style="left:100px;top:2497px" width="20" height="26" viewBox="0 0 24 30" aria-hidden="true">
  <path d="M5 2 L9 2 L11 9 L8 11 C9 16 12 20 15 22 L18 19 L23 22 L22 27 C20 29 16 29 12 26 C6 21 2 14 2 7 C2 4 3 2 5 2Z" fill="#fff"/>
</svg>
<div class="abs footer-text" style="left:127px">+31647208351</div>
<svg class="abs" style="left:262px;top:2501px" width="27" height="18" viewBox="0 0 48 32" aria-hidden="true">
  <rect x="1" y="1" width="46" height="30" fill="none" stroke="#fff" stroke-width="3"/>
  <path d="M2 2 L24 19 L46 2" fill="none" stroke="#fff" stroke-width="3"/>
</svg>
<div class="abs footer-text" style="left:301px">contact@skyloftreels.example</div>
<div class="abs copyright">COPYRIGHT © 2016 SKYLOFTREELS. ALL RIGHTS RESERVED.</div>

</body>
</html>
```